High Tech Real Estate Startup needs a business card

We are developing an innovative real estate marketing product based around advanced search and virtual reality.

We talk to people, we need business cards.

Target Market(s)

The target market is technology professionals and realtors.

Contact Information for Business Card

The information to be included will include

Name
Title
Phone Number
E-mail Address
www.zelquin.com

It should use simple iconography for each one of those fields.

Font styles to use
Other font styles liked:
• Co, Jubilat, Avenir

Colors

Designer to choose colors to be used in the design.

Requirements
Must have
• Clean aesthetic,
• Good use of negative space.
• It should use our company logo, shown in the attached file. It is able to use the negative of that logo (coloured font and white background) and I have attached other acceptable accent colours in a swatch file.
Should not have
• Should not be too busy
• No extraneous text (slogans, tag lines etc)

```html
<!DOCTYPE html>
<html lang="en">
<head>
<meta charset="UTF-8">
<title>Zelquin Business Card</title>
<link rel="stylesheet" href="https://fonts.googleapis.com/css2?family=Montserrat:wght@400;500;600&display=swap">
<style>
  :root {
    --stage: #2b2b2d;
    --card: #1c1d20;
    --teal: #3cc4c2;
    --white: #f4f4f4;
    --muted: #c9cbcd;
  }
  * { margin: 0; padding: 0; box-sizing: border-box; }
  html, body { width: 800px; height: 1200px; overflow: hidden; }
  body {
    background: var(--stage);
    font-family: "Montserrat", sans-serif;
    position: relative;
  }
  .card {
    position: absolute;
    left: 80px;
    width: 640px;
    height: 366px;
    background: var(--card);
    border-radius: 26px;
    overflow: hidden;
    box-shadow: 0 14px 30px rgba(0,0,0,0.35);
  }
  .card-front { top: 170px; }
  .card-back { top: 664px; }

  .wordmark {
    color: var(--teal);
    font-weight: 500;
    letter-spacing: 4px;
  }
  .card-front .wordmark {
    position: absolute;
    left: 0; right: 0; top: 146px;
    text-align: center;
    font-size: 64px;
    line-height: 1;
  }

  .holder { position: absolute; left: 40px; top: 38px; }
  .holder-name {
    color: var(--teal);
    font-size: 24px;
    font-weight: 500;
  }
  .holder-title {
    color: var(--white);
    font-size: 13px;
    margin-top: 4px;
  }

  .contact-list {
    position: absolute;
    left: 44px; top: 196px;
    list-style: none;
  }
  .contact-item {
    display: flex;
    align-items: center;
    gap: 12px;
    color: var(--muted);
    font-size: 13px;
    height: 24px;
  }
  .contact-icon { width: 13px; height: 13px; flex: none; }

  .card-back .wordmark {
    position: absolute;
    right: 36px; bottom: 40px;
    font-size: 50px;
    line-height: 1;
  }
  .edge-line {
    position: absolute;
    left: 0; bottom: 12px;
    width: 400px; height: 4px;
    background: var(--teal);
  }
  .edge-bar {
    position: absolute;
    left: 400px; right: 0; bottom: 0;
    height: 16px;
    background: var(--white);
  }
</style>
</head>
<body>
  <section class="card card-front">
    <div class="wordmark">ZELQUIN</div>
  </section>

  <section class="card card-back">
    <div class="holder">
      <div class="holder-name">Alex Marlow Reed</div>
      <div class="holder-title">Managing Director</div>
    </div>

    <ul class="contact-list">
      <li class="contact-item">
        <svg class="contact-icon" viewBox="0 0 16 16" aria-hidden="true">
          <path fill="var(--teal)" d="M3.6 1.2l2.3 2.6-1.3 1.8c.9 2 2.6 3.7 4.6 4.6l1.8-1.3 2.6 2.3-1.5 2.4C6.8 13.4 2.6 9.2 1.2 3.1z"/>
        </svg>
        555.014.2281
      </li>
      <li class="contact-item">
        <svg class="contact-icon" viewBox="0 0 16 16" aria-hidden="true">
          <rect x="1" y="3" width="14" height="10" rx="1" fill="var(--teal)"/>
          <path d="M1.5 3.8L8 8.8l6.5-5" fill="none" stroke="var(--card)" stroke-width="1.4"/>
        </svg>
        areed@zelquin.com
      </li>
      <li class="contact-item">
        <svg class="contact-icon" viewBox="0 0 16 16" aria-hidden="true">
          <g fill="none" stroke="var(--teal)" stroke-width="1.4">
            <circle cx="8" cy="8" r="6.3"/>
            <ellipse cx="8" cy="8" rx="2.8" ry="6.3"/>
            <path d="M1.7 8h12.6"/>
          </g>
        </svg>
        www.zelquin.com
      </li>
    </ul>

    <div class="wordmark">ZELQUIN</div>
    <div class="edge-line"></div>
    <div class="edge-bar"></div>
  </section>
</body>
</html>
```